New business card/stationary for a consulting company

I am looking for a clean and very professional looking business card for my consulting company as well as corresponding stationary. I am uploading our logo. I like simple and powerful for the feel. No graphics but I am open on everything else. Below is my contact information but would like the final to be in a version I can add my employees information into and print. Thank you.

Daniel Whitcombe
dan@ferncliffadvisory.com
2870 North 9th Avenue, Summit Floor, Elm Ridge, Illinois 60531
www.ferncliffadvisory.com

Industry/Entity Type

Consulting

Contact Information for Business Card

Daniel Whitcombe
dan@ferncliffadvisory.com
www.ferncliffadvisory.com

Font styles to use
Serif
Sans Serif

Requirements
Must have
• Our logo and the business card details.
Nice to have
• our website www.ferncliffadvisory.com

```html
<!DOCTYPE html>
<html lang="en">
<head>
<meta charset="utf-8">
<title>Ferncliff Advisory — Business Card</title>
<link rel="stylesheet" href="https://fonts.googleapis.com/css2?family=Lato:ital,wght@0,400;0,700;1,400&display=swap">
<style>
  :root {
    --navy: #07076a;
    --paper: #ffffff;
    --ink: #1c1c1c;
    --rule: #222222;
    --stage: #e9e9ec;
  }
  * { box-sizing: border-box; margin: 0; padding: 0; }
  html, body {
    width: 1200px; height: 900px; overflow: hidden;
    background: var(--stage);
    font-family: "Lato", Arial, sans-serif;
  }
  .stage {
    position: relative; width: 1200px; height: 900px;
  }
  .card {
    position: absolute; left: 250px; width: 700px; height: 400px;
    overflow: hidden;
    box-shadow: 0 6px 18px rgba(0,0,0,0.18);
  }
  .card--front { top: 36px; background: var(--navy); }
  .card--back  { top: 470px; background: var(--paper); }

  /* Brand lockup */
  .brand { position: absolute; display: flex; flex-direction: column; align-items: center; }
  .brand__square { width: 44px; height: 44px; margin-bottom: 14px; }
  .brand__name {
    font-family: "Lato", Arial, sans-serif; font-weight: 400;
    font-size: 34px; letter-spacing: 2px; text-transform: uppercase; white-space: nowrap;
  }
  .card--front .brand { left: 0; right: 0; top: 130px; }
  .card--front .brand__square { background: var(--paper); }
  .card--front .brand__name { color: var(--paper); }

  .card--back .brand { right: 40px; top: 38px; }
  .card--back .brand__square { background: var(--navy); width: 38px; height: 38px; margin-bottom: 10px; }
  .card--back .brand__name { color: var(--navy); font-size: 28px; }

  /* Person */
  .person__name {
    position: absolute; left: 48px; top: 140px;
    font-weight: 700; font-size: 30px; color: var(--navy); letter-spacing: -0.5px;
  }
  .person__rule-bold {
    position: absolute; left: 42px; top: 184px; width: 265px; height: 5px;
    background: var(--navy); border-radius: 3px;
  }
  .person__rule-thin {
    position: absolute; left: 300px; top: 186px; width: 360px; height: 1.5px;
    background: var(--rule);
  }

  .contact { position: absolute; color: var(--ink); font-size: 19px; line-height: 25px; }
  .contact svg { position: absolute; left: -30px; top: 3px; fill: var(--navy); }
  .contact--address { left: 70px; top: 200px; }
  .contact--email { left: 410px; top: 228px; }
  .contact--email svg { top: 5px; }

  .website {
    position: absolute; left: 0; right: 0; top: 320px; text-align: center;
    font-size: 20px; letter-spacing: 7px; color: var(--ink);
  }
  .card__band {
    position: absolute; left: 0; right: 0; bottom: 0; height: 16px; background: var(--navy);
  }
</style>
</head>
<body>
<main class="stage">

  <section class="card card--front" aria-label="Card front">
    <div class="brand">
      <div class="brand__square"></div>
      <div class="brand__name">Ferncliff Advisory</div>
    </div>
  </section>

  <section class="card card--back" aria-label="Card back">
    <div class="brand">
      <div class="brand__square"></div>
      <div class="brand__name">Ferncliff Advisory</div>
    </div>

    <h1 class="person__name">Daniel Whitcombe</h1>
    <div class="person__rule-bold"></div>
    <div class="person__rule-thin"></div>

    <address class="contact contact--address" style="font-style: normal;">
      <svg width="20" height="18" viewBox="0 0 20 18" aria-hidden="true">
        <path d="M10 1 L19 9 L16.5 9 L16.5 17 L12 17 L12 12 L8 12 L8 17 L3.5 17 L3.5 9 L1 9 Z"/>
      </svg>
      2870 North 9th Avenue<br>
      Summit Floor<br>
      Elm Ridge, Illinois 60531
    </address>

    <div class="contact contact--email">
      <svg width="20" height="14" viewBox="0 0 20 14" aria-hidden="true">
        <rect x="0.5" y="0.5" width="19" height="13" fill="none" stroke="#07076a" stroke-width="1.5"/>
        <path d="M1 1 L10 8 L19 1" fill="none" stroke="#07076a" stroke-width="1.5"/>
      </svg>
      dan@ferncliffadvisory.com
    </div>

    <div class="website">www.ferncliffadvisory.com</div>
    <div class="card__band"></div>
  </section>

</main>
</body>
</html>
```